Tech business card design

We need an amazing business card design for our new business 'Pexla' a marketing tech startup based in Sydney, Australia. We provide an online marketplace for businesses to search and buy advertising media, connect with service providers and learn more about marketing. We wish to communicate 'cool tech', reliability and professionalism and design based around our logo.

Target Market(s)

Business Owners

Contact Information for Business Card

Name
Position
Email Address
Website
Phone Number

Font styles to use
Other font styles liked:
• Avenir & Avenir Next

Colors

Designer to choose colors to be used in the design.

```html
<!DOCTYPE html>
<html lang="en">
<head>
<meta charset="utf-8">
<title>Pexla Business Card</title>
<link rel="stylesheet" href="https://fonts.googleapis.com/css2?family=Nunito+Sans:wght@400;600;800&display=swap">
<style>
  :root {
    --navy: #15144d;
    --navy-deep: #0c0b33;
    --navy-light: #24237a;
    --paper: #ffffff;
    --ink-grey: #6b6b78;
    --stage: #e9e9ee;
    --divider: #c9c9d2;
  }
  * { margin: 0; padding: 0; box-sizing: border-box; }
  html, body {
    width: 1200px; height: 892px; overflow: hidden;
    background: var(--stage);
    font-family: "Nunito Sans", "Avenir Next", Avenir, sans-serif;
  }
  .canvas { position: relative; width: 1200px; height: 892px; }
  .card {
    position: absolute; width: 560px; height: 320px;
    box-shadow: 0 10px 28px rgba(10, 10, 40, 0.22);
    overflow: hidden;
  }
  .card--front {
    left: 90px; top: 90px;
    background: radial-gradient(ellipse at 55% 30%, var(--navy-light) 0%, var(--navy) 50%, var(--navy-deep) 100%);
    color: var(--paper);
    text-align: center;
  }
  .front__wordmark {
    position: absolute; left: 0; right: 0; top: 78px;
    font-weight: 800; font-size: 118px; line-height: 1; letter-spacing: -2px;
    color: var(--paper);
  }
  .front__url {
    position: absolute; left: 0; right: 0; top: 236px;
    font-size: 13px; letter-spacing: 6px; font-weight: 400;
  }
  .card--back {
    left: 550px; top: 472px;
    background: var(--paper);
  }
  .back__band {
    position: absolute; left: 0; right: 0; bottom: 0; height: 26px;
    background: var(--navy);
  }
  .back__wordmark {
    position: absolute; left: 38px; top: 118px;
    font-weight: 800; font-size: 84px; line-height: 1; letter-spacing: -1.5px;
    color: var(--navy);
  }
  .back__divider {
    position: absolute; left: 292px; top: 60px; width: 1px; height: 170px;
    background: linear-gradient(to bottom, transparent, var(--divider) 30%, var(--divider) 70%, transparent);
  }
  .contact { position: absolute; left: 312px; top: 74px; }
  .contact__name {
    font-weight: 600; font-size: 18px; color: var(--navy); letter-spacing: 0.5px;
  }
  .contact__role {
    font-size: 13px; color: var(--ink-grey); letter-spacing: 1px; margin-bottom: 14px;
  }
  .contact__line {
    display: flex; align-items: center; gap: 9px;
    font-size: 12.5px; color: var(--ink-grey); margin-bottom: 5px;
  }
  .contact__icon { width: 13px; height: 13px; flex: none; }
</style>
</head>
<body>
<main class="canvas">
  <section class="card card--front" aria-label="Card front">
    <div class="front__wordmark">pexla</div>
    <div class="front__url">www.pexlamedia.com.au</div>
  </section>

  <section class="card card--back" aria-label="Card back">
    <div class="back__wordmark">pexla</div>
    <div class="back__divider"></div>
    <div class="contact">
      <div class="contact__name">DANIEL REEVE</div>
      <div class="contact__role">FOUNDER, DIRECTOR</div>
      <div class="contact__line">
        <svg class="contact__icon" viewBox="0 0 13 13"><rect x="3" y="0.5" width="7" height="12" rx="1.2" fill="none" stroke="#15144d" stroke-width="1.4"/><circle cx="6.5" cy="10.3" r="0.8" fill="#15144d"/></svg>
        +61 (0)412 555 208
      </div>
      <div class="contact__line">
        <svg class="contact__icon" viewBox="0 0 13 13"><rect x="0.5" y="2.5" width="12" height="8" fill="#15144d"/><path d="M0.5 2.5 L6.5 7 L12.5 2.5" fill="none" stroke="#fff" stroke-width="1"/></svg>
        daniel@pexlamedia.com.au
      </div>
      <div class="contact__line">
        <svg class="contact__icon" viewBox="0 0 13 13"><circle cx="6.5" cy="6.5" r="6" fill="#15144d"/><ellipse cx="6.5" cy="6.5" rx="2.5" ry="6" fill="none" stroke="#fff" stroke-width="0.8"/><line x1="0.5" y1="6.5" x2="12.5" y2="6.5" stroke="#fff" stroke-width="0.8"/></svg>
        www.pexlamedia.com.au
      </div>
    </div>
    <div class="back__band"></div>
  </section>
</main>
</body>
</html>
```